Letter and Envelope Design For Harborline Realty

Please design a letter and an envelope incorporating our logo (See Attached). We are also launched a business card contest. Since we want them to match, please feel free to submit a design for both the business card and also the letter design and envelope.

Requirements
Must have
• The envelope, the letter and the business cards must match somehow connecting the designs. We want them to have something that holds them together besides the logo.

```html
<!DOCTYPE html>
<html lang="en">
<head>
<meta charset="utf-8">
<title>Harborline Realty Stationery</title>
<link href="https://fonts.googleapis.com/css2?family=Montserrat:wght@500;600&family=Jost:wght@400;500&family=Arimo&display=swap" rel="stylesheet">
<style>
:root{
  --brand-blue:#0b1a8c;
  --brand-grey:#5a5a5e;
  --paper:#ffffff;
  --ink:#5c5c5c;
  --backdrop:#d6d6d8;
}
*{box-sizing:border-box;margin:0;padding:0}
html,body{width:1200px;height:768px;overflow:hidden;background:var(--backdrop)}
.canvas{position:relative;width:1200px;height:768px}
.sheet{position:absolute;background:var(--paper);box-shadow:0 4px 14px rgba(0,0,0,.12);overflow:hidden}
.sheet svg.bands{position:absolute;inset:0;width:100%;height:100%}
.wordmark{display:flex;align-items:center;gap:8px;font-family:"Montserrat",sans-serif;font-weight:600;letter-spacing:.08em;text-transform:uppercase;color:var(--brand-blue);white-space:nowrap}
.wordmark .dot{width:22px;height:22px;border-radius:50%;border:2px solid var(--brand-blue);flex:none}
.wordmark.on-blue{color:#fff}
.wordmark.on-blue .dot{border-color:#fff}

/* letterhead */
.letterhead{left:670px;top:60px;width:450px;height:636px}
.letterhead .contact{position:absolute;right:16px;top:12px;text-align:right;font-family:"Jost",sans-serif;font-size:6.5px;line-height:1.45;color:#fff}
.letterhead .wordmark{position:absolute;left:40px;top:112px;font-size:15px}
.letterhead .body{position:absolute;left:40px;right:40px;top:168px;font-family:"Arimo",sans-serif;font-size:9.2px;line-height:1.55;color:var(--ink)}
.letterhead .body p{margin-bottom:12px}

/* envelope */
.envelope{left:60px;top:470px;width:560px;height:244px}
.envelope .wordmark{position:absolute;left:30px;top:28px;font-size:13px}
.envelope .return{position:absolute;left:60px;top:58px;font-family:"Jost",sans-serif;font-size:8px;color:var(--brand-blue)}

/* business cards */
.card{width:290px;height:166px}
.card-front{left:60px;top:60px;background:var(--brand-blue)}
.card-front .wordmark{position:absolute;left:0;right:0;top:70px;justify-content:center;font-size:14px}
.card-back{left:370px;top:60px}
.card-back .wordmark{position:absolute;left:16px;top:66px;font-size:9px;gap:6px;letter-spacing:.06em}
.card-back .wordmark .dot{width:15px;height:15px}
.card-back .details{position:absolute;left:172px;top:38px;padding-left:9px;border-left:1px solid var(--brand-grey);font-family:"Jost",sans-serif;font-size:6.5px;line-height:1.6;color:var(--brand-grey)}
.card-back .details .name{font-family:"Montserrat",sans-serif;font-weight:600;font-size:9px;color:var(--brand-blue)}
.card-back .details .role{font-size:6.5px;margin-bottom:3px}
.card-back .details li{list-style:none;display:flex;align-items:center;gap:4px}
.card-back .details li::before{content:"";width:5px;height:5px;border-radius:50%;background:var(--brand-blue);flex:none}
</style>
</head>
<body>
<div class="canvas">

  <section class="sheet card card-front">
    <div class="wordmark on-blue"><span class="dot"></span>Harborline Realty</div>
  </section>

  <section class="sheet card card-back">
    <svg class="bands" viewBox="0 0 290 166" preserveAspectRatio="none">
      <polygon points="230,0 290,0 290,22" fill="var(--brand-blue)"/>
      <line x1="214" y1="0" x2="290" y2="30" stroke="var(--brand-grey)" stroke-width="2"/>
      <polygon points="0,166 0,146 70,166" fill="var(--brand-blue)"/>
      <line x1="0" y1="138" x2="90" y2="166" stroke="var(--brand-grey)" stroke-width="2"/>
    </svg>
    <div class="wordmark"><span class="dot"></span>Harborline Realty</div>
    <div class="details">
      <div class="name">Example Name</div>
      <div class="role">Designation</div>
      <ul>
        <li>Example 00, Example Street, US</li>
        <li>000.000.0000</li>
        <li>000.000.0000</li>
        <li>info@harborlinerealty.com</li>
        <li>www.harborlinerealty.com</li>
      </ul>
    </div>
  </section>

  <section class="sheet envelope">
    <svg class="bands" viewBox="0 0 560 244" preserveAspectRatio="none">
      <polygon points="560,244 400,244 560,170" fill="var(--brand-blue)"/>
      <line x1="370" y1="244" x2="560" y2="156" stroke="var(--brand-grey)" stroke-width="2"/>
    </svg>
    <div class="wordmark"><span class="dot"></span>Harborline Realty</div>
    <div class="return">Example 00, Example Street, US, 0000</div>
  </section>

  <section class="sheet letterhead">
    <svg class="bands" viewBox="0 0 450 636" preserveAspectRatio="none">
      <polygon points="150,0 450,0 450,80" fill="var(--brand-blue)"/>
      <line x1="120" y1="0" x2="450" y2="96" stroke="var(--brand-grey)" stroke-width="2"/>
      <polygon points="0,636 0,560 260,636" fill="var(--brand-blue)"/>
      <line x1="0" y1="540" x2="310" y2="636" stroke="var(--brand-grey)" stroke-width="2"/>
    </svg>
    <div class="contact">
      0000 Example Road<br>
      Suite 000, Riverton, US 00000<br>
      000.000.0000 | 000.000.0000<br>
      info@harborlinerealty.com<br>
      www.harborlinerealty.com
    </div>
    <div class="wordmark"><span class="dot"></span>Harborline Realty</div>
    <div class="body">
      <p>Lorem Ipsum is simply dummy text of the printing and typesetting industry. Lorem Ipsum has been the industry's standard dummy text ever since the 1500s, when an unknown printer took a galley of type and scrambled it to make a type specimen book. It has survived not only five centuries, but also the leap into electronic typesetting, remaining essentially unchanged. It was popularised in the 1960s with the release of Transfix sheets containing Lorem Ipsum passages, and more recently with desktop publishing software like Folio Layout including versions of Lorem Ipsum.</p>
      <p>It is a long established fact that a reader will be distracted by the readable content of a page when looking at its layout. The point of using Lorem Ipsum is that it has a more-or-less normal distribution of letters, as opposed to using 'Content here, content here', making it look like readable English. Many desktop publishing packages and web page editors now use Lorem Ipsum as their default model text, and a search for 'lorem ipsum' will uncover many web sites still in their infancy. Various versions have evolved over the years, sometimes by accident, sometimes on purpose (injected humour and the like).</p>
      <p>Contrary to popular belief, Lorem Ipsum is not simply random text. It has roots in a piece of classical Latin literature, making it over 2000 years old. Daniel Corwin, a Latin professor in Alderbrook, looked up one of the more obscure Latin words from a passage, and going through the cites of the word in classical literature, discovered the undoubtable source. Lorem Ipsum comes from sections 1.10.32 and 1.10.33 of an old treatise on ethics. The generated Lorem Ipsum is therefore always free from repetition, injected humour, or non-characteristic words.</p>
    </div>
  </section>

</div>
</body>
</html>
```